Modern Verdell Tree Care Website

I need a website for a full service Tree Care company. The company provides tree pruning, tree removal, tree preservation, emergency services, stump grinding, and emergency tree services.

Target Market(s)

Customers that need tree services

Industry/Entity Type

Landscaping, Tree Services

Coding

Coded - Design and coding required

Number of Pages Required

5+ page

Font styles to use
Sans Serif

Requirements
Must have
• Good clean design that showcases the services the company provides.
Nice to have
• Services page; contact form, blog, home page, about page

```html
<!DOCTYPE html>
<html lang="en">
<head>
<meta charset="utf-8">
<title>Verdell Tree Care</title>
<link rel="stylesheet" href="https://fonts.googleapis.com/css2?family=Fira+Sans:wght@500;600&family=Lato:wght@400;700&display=swap">
<style>
:root{
  --navy:#1b2e6e;
  --deep:#1d3950;
  --green:#8cc63f;
  --orange:#f6a733;
  --topbar:#5d6a6c;
  --light:#f2f5f8;
  --panel:#eef2f7;
  --text:#3d4a7a;
  --white:#fff;
}
*{box-sizing:border-box;margin:0;padding:0}
html,body{width:1200px;height:4317px;overflow:hidden}
body{position:relative;font-family:"Lato",sans-serif;color:var(--text);background:var(--white)}
.abs{position:absolute}
.heading{font-family:"Fira Sans",sans-serif;font-weight:600;color:var(--navy);font-size:47px;line-height:61px}
.eyebrow{font-size:12px;font-weight:700;color:var(--green);letter-spacing:.3px;display:flex;align-items:center;gap:14px}
.eyebrow::after{content:"";width:48px;height:2px;background:var(--green)}
.btn{background:var(--green);color:#fff;font-weight:700;font-size:14px;display:flex;align-items:center;justify-content:center;border-radius:3px}
.para{font-size:13.5px;line-height:24px;color:var(--navy)}
.topbar{left:0;top:0;width:1200px;height:34px;background:var(--topbar);color:#fff;font-size:12px;display:flex;align-items:center;justify-content:center;gap:6px}
.header{left:0;top:34px;width:1200px;height:110px;background:#fff}
.brand{display:flex;align-items:center;gap:10px;font-family:"Fira Sans",sans-serif;font-weight:600;font-size:24px;color:var(--navy)}
.brand-mark{width:38px;height:38px;background:var(--green)}
.nav a{position:absolute;top:0;font-size:12.5px;font-weight:700;color:#1f2a44;text-decoration:none}
.hero-photo{left:0;top:144px;width:1200px;height:700px;background:linear-gradient(100deg,#8c9c9f 0%,#9fb0a8 30%,#6f8a55 55%,#5b4a38 75%,#9b8b6a 100%)}
.hero-fade{left:0;top:144px;width:560px;height:560px;background:linear-gradient(90deg,rgba(90,105,112,.55),rgba(90,105,112,0))}
.hero-text{color:#fff}
.arrow-box{width:44px;height:64px;background:#fff;box-shadow:0 2px 8px rgba(0,0,0,.1);display:flex;align-items:center;justify-content:center;color:#222;font-size:22px}
.card{width:321px;height:401px;background:#fff;box-shadow:0 2px 10px rgba(0,0,0,.06);text-align:center}
.card-photo{width:100%;height:210px}
.card-icon{position:absolute;left:125px;top:175px;width:70px;height:70px;border-radius:50%;background:var(--navy);border:4px solid #fff;display:flex;align-items:center;justify-content:center}
.card h3{position:absolute;top:265px;width:100%;font-family:"Fira Sans",sans-serif;font-weight:600;font-size:23px;color:var(--navy)}
.card p{position:absolute;top:305px;left:30px;right:30px;font-size:13.5px;line-height:24px;color:#333}
.card .rule{position:absolute;top:372px;left:142px;width:38px;height:2px;background:var(--green)}
.feature h4{font-family:"Fira Sans",sans-serif;font-size:15.5px;font-weight:500;color:var(--navy)}
.feature p{font-size:13.5px;line-height:24px;color:var(--text);margin-top:8px;padding-left:4px}
.quote-card{width:320px;height:241px;background:var(--panel);border-radius:22px}
.quote-mark{font-family:"Fira Sans",sans-serif;font-size:90px;line-height:1;color:var(--green);font-weight:600}
.stars{color:#f6b21b;font-size:16px;letter-spacing:2px}
.quote-body h5{font-size:16px;font-weight:700;color:#222;margin-top:6px}
.quote-body p{font-size:12.5px;line-height:24px;color:#333;margin-top:6px}
.avatar{width:44px;height:44px;border-radius:50%;background:#b9c0c8}
.person b{display:block;color:var(--green);font-family:"Fira Sans",sans-serif;font-weight:500;font-size:17px}
.person span{font-size:11px;color:#333}
.field{background:#fff;border:1px solid #e3e7ec;border-radius:3px;font-size:11.5px;color:#999;padding:10px 16px}
.footer{left:0;top:3945px;width:1200px;height:372px;background:var(--deep);color:#fff}
.footer h6{font-size:15px;font-weight:700}
.footer .item{font-size:11.5px;line-height:20px}
.social{width:38px;height:36px;border:1px solid #fff}
</style>
</head>
<body>

<div class="abs topbar">
  <svg width="10" height="13" viewBox="0 0 10 13"><path d="M5 0a5 5 0 0 0-5 5c0 3.5 5 8 5 8s5-4.5 5-8a5 5 0 0 0-5-5zm0 7a2 2 0 1 1 0-4 2 2 0 0 1 0 4z" fill="#fff"/></svg>
  4820 Larchwood Lane
</div>

<header class="abs header">
  <div class="abs brand" style="left:95px;top:23px"><span class="brand-mark"></span>Verdell Tree Care</div>
  <div class="abs" style="left:689px;top:24px;font-size:16px;color:var(--navy);display:flex;align-items:center;gap:7px">
    <svg width="15" height="15" viewBox="0 0 24 24"><path d="M6.6 10.8a15.1 15.1 0 0 0 6.6 6.6l2.2-2.2c.3-.3.7-.4 1-.2 1.1.4 2.3.6 3.6.6.6 0 1 .4 1 1V20c0 .6-.4 1-1 1A17 17 0 0 1 3 4c0-.6.4-1 1-1h3.5c.6 0 1 .4 1 1 0 1.3.2 2.5.6 3.6.1.3 0 .7-.2 1z" fill="var(--navy)"/></svg>
    (555) 014-2290</div>
  <div class="abs btn" style="left:858px;top:15px;width:191px;height:40px;font-size:12.5px">REQUEST APPOINTMENT</div>
  <nav class="abs nav" style="left:0;top:77px;width:1200px">
    <a style="left:422px;color:var(--navy)">HOME</a>
    <a style="left:513px">ABOUT US</a>
    <a style="left:637px">SERVICES</a>
    <a style="left:756px">OUR TEAM</a>
    <a style="left:887px">GALLERY</a>
    <a style="left:1004px">CONTACT US</a>
  </nav>
  <div class="abs" style="left:414px;top:105px;width:60px;height:3px;background:var(--navy)"></div>
</header>

<section>
  <div class="abs hero-photo" role="img" aria-label="Arborist cutting a large tree trunk with a chainsaw among green trees"></div>
  <div class="abs hero-fade"></div>
  <div class="abs hero-text" style="left:90px;top:340px;font-size:13px;display:flex;align-items:center;gap:22px">Welcome<span style="width:44px;height:1px;background:#fff"></span></div>
  <h1 class="abs hero-text" style="left:90px;top:370px;font-family:'Fira Sans',sans-serif;font-weight:500;font-size:41px;line-height:58px">Your Partner in<br>Tree Presevation</h1>
  <p class="abs hero-text" style="left:90px;top:500px;width:410px;font-size:13.5px;line-height:21px">Lorem ipsum dolor sit amet, consectetur adipiscing elit, sed do eiusmod tempor incididunt ut labore et dolore magna Lorem ipsum dolor sit amet, consectetur adipiscing elit, sed do eiusmod tempor incididunt ut labore et dolore magna</p>
  <div class="abs btn" style="left:90px;top:613px;width:193px;height:42px;border-radius:0;font-size:13px">Discover more</div>
  <svg class="abs" style="left:0;top:720px" width="1200" height="130" viewBox="0 0 1200 130">
    <path d="M0 40 C300 130 700 120 1200 30 L1200 130 L0 130Z" fill="var(--light)"/>
    <path d="M0 45 C300 130 700 125 1200 10 L1200 22 C700 115 300 125 0 45Z" fill="var(--green)"/>
    <path d="M0 50 C320 150 760 130 1200 30 L1200 42 C760 138 320 150 0 50Z" fill="var(--orange)"/>
  </svg>
</section>

<section class="abs" style="left:0;top:848px;width:1200px;height:700px;background:var(--light)">
  <div class="abs eyebrow" style="left:100px;top:80px">OUR TREATMENTS</div>
  <h2 class="abs heading" style="left:97px;top:110px">Services We Provide</h2>
  <div class="abs arrow-box" style="left:1011px;top:94px">‹</div>
  <div class="abs arrow-box" style="left:1064px;top:94px">›</div>
  <article class="abs card" style="left:94px;top:206px">
    <div class="card-photo" role="img" aria-label="Worker pruning branches with red loppers" style="background:linear-gradient(135deg,#5d7a3a,#a9b38a)"></div>
    <div class="card-icon"><svg width="30" height="30" viewBox="0 0 24 24" fill="none" stroke="#fff" stroke-width="1.6"><path d="M12 3l2.6 2.4 3.5-.3.3 3.5L21 12l-2.6 2.6.3 3.5-3.5.3L12 21l-2.6-2.6-3.5-.3-.3-3.5L3 12l2.6-2.6-.3-3.5 3.5.3z"/></svg></div>
    <h3>Tree Pruning</h3>
    <p>Lorem ipsum dolor sit amet, consectetur adi piscing elit sed do eiusmod tmpor</p>
    <div class="rule"></div>
  </article>
  <article class="abs card" style="left:442px;top:206px">
    <div class="card-photo" role="img" aria-label="Freshly cut tree stump with sawdust on grass" style="background:linear-gradient(135deg,#6a6a35,#b49a64)"></div>
    <div class="card-icon"><svg width="30" height="30" viewBox="0 0 24 24" fill="none" stroke="#fff" stroke-width="1.6"><path d="M6 20h12M9 17l6-10M13 5l3 2M8 14l3 2"/></svg></div>
    <h3>Tree Removal</h3>
    <p>Lorem ipsum dolor sit amet, consectetur adi piscing elit sed do eiusmod tmpor</p>
    <div class="rule"></div>
  </article>
  <article class="abs card" style="left:791px;top:206px">
    <div class="card-photo" role="img" aria-label="Two people tending a hedge row in a garden" style="background:linear-gradient(135deg,#3f6b34,#9bc07a)"></div>
    <div class="card-icon"><svg width="30" height="30" viewBox="0 0 24 24" fill="none" stroke="#fff" stroke-width="1.6"><circle cx="9" cy="8" r="3"/><circle cx="16" cy="9" r="2.5"/><path d="M3 19c0-3 3-5 6-5s6 2 6 5M15 14c3 0 6 1.5 6 4"/></svg></div>
    <h3>Stump Grinding</h3>
    <p>Lorem ipsum dolor sit amet, consectetur adi piscing elit sed do eiusmod tmpor</p>
    <div class="rule"></div>
  </article>
</section>

<section>
  <div class="abs eyebrow" style="left:97px;top:1632px">TREATMENTS</div>
  <h2 class="abs heading" style="left:94px;top:1663px">We Offer Sustainable<br>Tree Solutions</h2>
  <p class="abs para" style="left:97px;top:1798px;width:460px">Lorem ipsum dolor sit amet, consectetur adipiscing elit, sed do eiusmo empor incididunt ut abore et dolore magna aliqua. Ut enim ad minim iam, quis nostrud exercitation ullamco</p>
  <div class="abs feature" style="left:104px;top:1900px;display:flex;gap:20px">
    <svg width="34" height="34" viewBox="0 0 24 24" fill="none" stroke="var(--green)" stroke-width="1.3"><circle cx="12" cy="12" r="3"/><path d="M12 2v3M12 19v3M2 12h3M19 12h3M5 5l2 2M17 17l2 2M5 19l2-2M17 7l2-2"/></svg>
    <div><h4>Quality Assurance</h4><p>Lorem ipsum dolor sit amet,<br>consectetur adipiscing</p></div>
  </div>
  <div class="abs feature" style="left:376px;top:1900px;display:flex;gap:20px">
    <svg width="34" height="34" viewBox="0 0 24 24" fill="none" stroke="var(--green)" stroke-width="1.3"><circle cx="10" cy="10" r="7"/><circle cx="17" cy="17" r="3"/></svg>
    <div><h4>Professional</h4><p>Lorem ipsum dolor sit amet,<br>consectetur adipiscing</p></div>
  </div>
  <div class="abs feature" style="left:104px;top:1997px;display:flex;gap:20px">
    <svg width="34" height="34" viewBox="0 0 24 24" fill="none" stroke="var(--green)" stroke-width="1.3"><circle cx="12" cy="8" r="4"/><path d="M4 21c0-4 4-6 8-6s8 2 8 6z"/></svg>
    <div><h4>Comprehensive Services</h4><p>Lorem ipsum dolor sit amet,<br>consectetur adipiscing</p></div>
  </div>
  <div class="abs feature" style="left:376px;top:1997px;display:flex;gap:20px">
    <svg width="34" height="34" viewBox="0 0 24 24" fill="none" stroke="var(--green)" stroke-width="1.3"><path d="M12 3l2.6 5.5 6 .7-4.4 4.1 1.2 6L12 16.4 6.6 19.3l1.2-6L3.4 9.2l6-.7z"/></svg>
    <div><h4>Client-centric</h4><p>Lorem ipsum dolor sit amet,<br>consectetur adipiscing</p></div>
  </div>
  <div class="abs btn" style="left:104px;top:2112px;width:168px;height:45px">Apply Now</div>
  <svg class="abs" style="left:640px;top:1650px" width="480" height="480" viewBox="0 0 480 480">
    <path d="M240 8 A232 232 0 1 1 20 170" fill="none" stroke="var(--orange)" stroke-width="9"/>
  </svg>
  <div class="abs" role="img" aria-label="Workers cutting a fallen tree trunk with a chainsaw" style="left:657px;top:1667px;width:446px;height:446px;border-radius:50%;background:radial-gradient(circle at 40% 40%,#8a7a5a,#4d6b3a 70%,#3a4f2e)"></div>
</section>

<section>
  <div class="abs" role="img" aria-label="Climber in safety gear working high up a bare tree" style="left:0;top:2232px;width:590px;height:446px;border:7px solid var(--green);background:linear-gradient(160deg,#b9c6d6,#5f6f8e 55%,#2f4578)"></div>
  <div class="abs" style="left:590px;top:2254px;width:610px;height:399px;background:var(--panel)"></div>
  <div class="abs eyebrow" style="left:649px;top:2297px">ABOUT US</div>
  <h2 class="abs heading" style="left:649px;top:2325px">Your Tree Care<br>Professionals</h2>
  <p class="abs para" style="left:649px;top:2462px;width:460px">Lorem ipsum dolor sit amet, consectetur adipiscing elit, sed do eiusmo empor incididunt ut abore et dolore magna aliqua. Ut enim ad minim iam, quis nostrud exercitation ullamco</p>
  <div class="abs btn" style="left:649px;top:2566px;width:168px;height:45px">Apply Now</div>
</section>

<section>
  <div class="abs eyebrow" style="left:96px;top:2764px">TESTIMONIALS</div>
  <h2 class="abs heading" style="left:93px;top:2797px">What Clients Are Saying</h2>
  <div class="abs arrow-box" style="left:1006px;top:2780px">‹</div>
  <div class="abs arrow-box" style="left:1059px;top:2780px">›</div>

  <div class="abs quote-card" style="left:92px;top:2911px"></div>
  <div class="abs quote-mark" style="left:122px;top:2875px">“</div>
  <div class="abs quote-body" style="left:124px;top:2946px;width:270px">
    <div class="stars">★★★★★</div><h5>They are the Best</h5>
    <p>Lorem ipsum dolor sit amet, consectetur adipiscing elit, sed do eiusmod tempor i ncididunt ut labore et dolore magna aliqua. Ut enim ad minim veniam, quis nostrud exercitation ullamco laboris nisi ut</p>
  </div>
  <div class="abs avatar" style="left:126px;top:3191px" role="img" aria-label="Client portrait"></div>
  <div class="abs person" style="left:186px;top:3190px"><b>Renata</b><span>CEO, Abc Company</span></div>

  <div class="abs quote-card" style="left:439px;top:2911px"></div>
  <div class="abs quote-mark" style="left:469px;top:2875px">“</div>
  <div class="abs quote-body" style="left:471px;top:2946px;width:270px">
    <div class="stars">★★★★★</div><h5>They are the Best</h5>
    <p>Lorem ipsum dolor sit amet, consectetur adipiscing elit, sed do eiusmod tempor i ncididunt ut labore et dolore magna aliqua. Ut enim ad minim veniam, quis nostrud exercitation ullamco laboris nisi ut</p>
  </div>
  <div class="abs avatar" style="left:473px;top:3191px" role="img" aria-label="Client portrait"></div>
  <div class="abs person" style="left:533px;top:3190px"><b>Renata</b><span>CEO, Abc Company</span></div>

  <div class="abs quote-card" style="left:784px;top:2911px"></div>
  <div class="abs quote-mark" style="left:814px;top:2875px">“</div>
  <div class="abs quote-body" style="left:816px;top:2946px;width:270px">
    <div class="stars">★★★★★</div><h5>They are the Best</h5>
    <p>Lorem ipsum dolor sit amet, consectetur adipiscing elit, sed do eiusmod tempor i ncididunt ut labore et dolore magna aliqua. Ut enim ad minim veniam, quis nostrud exercitation ullamco laboris nisi ut</p>
  </div>
  <div class="abs avatar" style="left:818px;top:3191px" role="img" aria-label="Client portrait"></div>
  <div class="abs person" style="left:878px;top:3190px"><b>Renata</b><span>CEO, Abc Company</span></div>
</section>

<section class="abs" style="left:0;top:3312px;width:1200px;height:640px;background:var(--light)">
  <div class="abs eyebrow" style="left:136px;top:74px">GET IN TOUCH</div>
  <h2 class="abs heading" style="left:133px;top:106px">Contact Us</h2>
  <p class="abs" style="left:138px;top:177px;font-size:12px;color:#555">Just send a message, we will answer within 24 hours</p>
  <div class="abs field" style="left:134px;top:233px;width:198px;height:37px">Your full name</div>
  <div class="abs field" style="left:353px;top:233px;width:198px;height:37px">Phone Number</div>
  <div class="abs field" style="left:134px;top:285px;width:198px;height:37px">Mail Address</div>
  <div class="abs field" style="left:353px;top:285px;width:198px;height:37px">Subject</div>
  <div class="abs field" style="left:134px;top:337px;width:417px;height:84px">Type your message...</div>
  <div class="abs btn" style="left:134px;top:446px;width:417px;height:35px;font-size:12px">Send Your Message</div>
  <div class="abs" role="img" aria-label="Climber sawing a thick branch against a blue sky" style="left:608px;top:85px;width:486px;height:396px;background:linear-gradient(150deg,#3f7fd0,#6a9de0 45%,#6b5a44 70%,#3d5a2a)"></div>
</section>

<svg class="abs" style="left:0;top:3860px" width="1200" height="100" viewBox="0 0 1200 100">
  <path d="M0 100 C300 20 800 0 1200 55 L1200 100Z" fill="var(--deep)"/>
  <path d="M0 95 C300 10 800 -5 1200 40 L1200 52 C800 5 300 20 0 95Z" fill="var(--green)"/>
  <path d="M0 85 C300 0 800 -15 1200 22 L1200 32 C800 -5 300 10 0 85Z" fill="var(--orange)"/>
</svg>

<footer class="abs footer">
  <div class="abs brand" style="left:0;width:1200px;top:48px;justify-content:center;color:#fff;font-size:26px"><span class="brand-mark" style="background:#fff"></span>Verdell Tree Care</div>
  <h6 class="abs" style="left:94px;top:113px">CONTACT US</h6>
  <svg class="abs" style="left:94px;top:150px" width="14" height="18" viewBox="0 0 10 13"><path d="M5 0a5 5 0 0 0-5 5c0 3.5 5 8 5 8s5-4.5 5-8a5 5 0 0 0-5-5zm0 7a2 2 0 1 1 0-4 2 2 0 0 1 0 4z" fill="#fff"/></svg>
  <div class="abs item" style="left:127px;top:148px">101- lorem ipsum simple text<br>print type text industry text.</div>
  <svg class="abs" style="left:94px;top:211px" width="14" height="14" viewBox="0 0 24 24"><path d="M6.6 10.8a15.1 15.1 0 0 0 6.6 6.6l2.2-2.2c.3-.3.7-.4 1-.2 1.1.4 2.3.6 3.6.6.6 0 1 .4 1 1V20c0 .6-.4 1-1 1A17 17 0 0 1 3 4c0-.6.4-1 1-1h3.5c.6 0 1 .4 1 1 0 1.3.2 2.5.6 3.6.1.3 0 .7-.2 1z" fill="#fff"/></svg>
  <div class="abs item" style="left:127px;top:208px">555 014 2290</div>
  <svg class="abs" style="left:94px;top:250px" width="16" height="11" viewBox="0 0 16 11"><rect width="16" height="11" fill="#fff"/><path d="M0 0l8 6 8-6" fill="none" stroke="var(--deep)" stroke-width="1.3"/></svg>
  <div class="abs item" style="left:127px;top:245px">hello@verdell.example</div>
  <p class="abs item" style="left:455px;top:155px;width:290px;text-align:center">Lorem ipsum dolor sit amet, consectetur adipisc ing elit, sed do eiusmod tempor incididunt bbbbbut bcbbbcbnmx zjzmsmmzm</p>
  <div class="abs social" style="left:536px;top:240px"></div>
  <div class="abs social" style="left:581px;top:240px"></div>
  <div class="abs social" style="left:625px;top:240px"></div>
  <h6 class="abs" style="right:94px;top:113px">OPENING HOURS</h6>
  <div class="abs item" style="right:127px;top:155px;text-align:right">Mon - Fri: 9am - to - 6pm</div>
  <div class="abs item" style="right:127px;top:187px;text-align:right">Saturday 9am - to - 2pm</div>
  <div class="abs item" style="right:127px;top:218px;text-align:right">Sunday : <u>Closed</u></div>
  <svg class="abs" style="right:94px;top:158px" width="15" height="15" viewBox="0 0 24 24" fill="none" stroke="#fff" stroke-width="2"><circle cx="12" cy="12" r="10"/><path d="M12 6v6l4 2"/></svg>
  <svg class="abs" style="right:94px;top:190px" width="15" height="15" viewBox="0 0 24 24" fill="none" stroke="#fff" stroke-width="2"><circle cx="12" cy="12" r="10"/><path d="M12 6v6l4 2"/></svg>
  <svg class="abs" style="right:94px;top:221px" width="15" height="15" viewBox="0 0 24 24" fill="none" stroke="#fff" stroke-width="2"><circle cx="12" cy="12" r="10"/><path d="M12 6v6l4 2"/></svg>
  <div class="abs" style="left:63px;top:309px;width:1074px;height:1px;background:rgba(255,255,255,.3)"></div>
  <div class="abs item" style="left:0;width:1200px;top:338px;text-align:center">Verdell Tree Care</div>
</footer>

</body>
</html>
```